Business Card and Letterhead for Pimlu - modern real estate business

I need a double sided business card design for Pimlu. Please see business card brief here https://files.trelvonadocs.com/sheet/r/7QzTmWbaXLJnoPEd-kRyUgFhHsstbvCe2qfoMxDa_pz/view?mode=shared

Please feel free to design the business cards however you feel best. I am happy to give some creative freedoms and then provide feedback from there.

Please then also create a letterhead to match the business card design

Colors

Designer to choose colors to be used in the design.

Requirements
Must have
• Must be a modern, elegant business card which looks very professional

```html
<!DOCTYPE html>
<html lang="en">
<head>
<meta charset="utf-8">
<title>Pimlu Business Card</title>
<link href="https://fonts.googleapis.com/css2?family=Montserrat:wght@400;500;600;700&display=swap" rel="stylesheet">
<style>
  :root {
    --stage: #2b2b2b;
    --card-black: #060606;
    --stripe: #1e1e1e;
    --brand-red: #e31e26;
    --paper: #ffffff;
    --ink: #1a1a1a;
    --light-text: #f2f2f2;
  }
  * { box-sizing: border-box; margin: 0; padding: 0; }
  html, body {
    width: 1200px; height: 900px; overflow: hidden;
    background: var(--stage);
    font-family: "Montserrat", sans-serif;
  }
  .canvas {
    position: relative; width: 1200px; height: 900px;
    background: radial-gradient(circle at 50% 40%, #3a3a3a, var(--stage) 70%);
  }
  .card {
    position: absolute; left: 250px; width: 700px; height: 400px;
    background: var(--card-black); overflow: hidden;
  }
  .card-front { top: 30px; }
  .card-back { top: 470px; }
  .card-art { position: absolute; inset: 0; width: 100%; height: 100%; }

  .brand-name {
    position: absolute; top: 130px; left: 0; right: 0; text-align: center;
    color: var(--brand-red); font-weight: 700; font-size: 104px;
    letter-spacing: 8px; line-height: 1;
  }
  .front-url {
    position: absolute; bottom: 44px; left: 0; right: 0; text-align: center;
    color: var(--light-text); font-size: 15px; letter-spacing: 1px;
  }
  .front-url strong { color: var(--brand-red); font-weight: 700; }

  .portrait {
    position: absolute; left: 118px; top: 32px; width: 156px; height: 156px;
    border-radius: 50%; border: 5px solid var(--paper);
    background: linear-gradient(160deg, #9fae7c 0%, #b9b59a 35%, #4a4a46 70%, #2a2a2a 100%);
  }
  .agent {
    position: absolute; left: 100px; top: 200px;
  }
  .agent-name {
    color: var(--brand-red); font-weight: 600; font-size: 26px;
    text-transform: uppercase; letter-spacing: 1px; line-height: 1.1;
  }
  .agent-title { color: var(--light-text); font-size: 17px; margin-top: 2px; }

  .contact {
    position: absolute; right: 60px; top: 258px; text-align: right;
    color: var(--ink); font-size: 17px; line-height: 1.25;
  }
  .address { margin-bottom: 8px; }
  .contact-line { display: flex; justify-content: flex-end; align-items: center; gap: 14px; }
  .contact-line svg { width: 16px; height: 16px; flex: none; }
</style>
</head>
<body>
<main class="canvas">

  <section class="card card-front">
    <svg class="card-art" viewBox="0 0 700 400" aria-hidden="true">
      <polygon points="175,0 200,0 330,240 315,240" fill="var(--stripe)"/>
      <polygon points="245,0 270,0 360,170 345,170" fill="var(--stripe)"/>
      <polygon points="140,400 160,400 330,240 315,240" fill="var(--stripe)"/>
    </svg>
    <div class="brand-name">PIMLU</div>
    <div class="front-url">www.<strong>pimlu</strong>.com</div>
  </section>

  <section class="card card-back">
    <svg class="card-art" viewBox="0 0 700 400" aria-hidden="true">
      <path d="M0 285 C120 315 270 335 420 268 C540 215 640 205 700 205 L700 400 L0 400Z" fill="var(--brand-red)"/>
      <path d="M0 310 C150 345 300 335 430 283 C540 235 640 222 700 222 L700 400 L0 400Z" fill="var(--card-black)"/>
      <path d="M40 296 C200 336 340 332 440 298 C340 346 180 346 40 296Z" fill="var(--brand-red)"/>
      <path d="M0 345 C170 372 330 345 450 292 C550 248 640 240 700 240 L700 400 L0 400Z" fill="var(--paper)"/>
    </svg>

    <div class="portrait" role="img" aria-label="Portrait photo of the agent outdoors"></div>

    <div class="agent">
      <div class="agent-name">Liam Carter</div>
      <div class="agent-title">Licenced Real Estate Agent</div>
    </div>

    <div class="contact">
      <div class="address">PO Box 1187<br>Brindale NSW 2790</div>
      <div class="contact-line">0412 386 590
        <svg viewBox="0 0 16 16" aria-hidden="true"><path d="M4 1.5l2.5 3-1.5 1.5c.8 1.8 2.2 3.2 4 4l1.5-1.5 3 2.5-1.5 2.5C7 13 3 9 1.5 3z" fill="var(--brand-red)"/></svg>
      </div>
      <div class="contact-line">liam@pimlu.com
        <svg viewBox="0 0 16 16" aria-hidden="true"><rect x="1.5" y="3.5" width="13" height="9" rx="1" fill="none" stroke="var(--brand-red)" stroke-width="1.4"/><path d="M1.5 4l6.5 5 6.5-5" fill="none" stroke="var(--brand-red)" stroke-width="1.4"/></svg>
      </div>
      <div class="contact-line">www.pimlu.com
        <svg viewBox="0 0 16 16" aria-hidden="true"><g fill="none" stroke="var(--brand-red)" stroke-width="1.2"><circle cx="8" cy="8" r="6.5"/><ellipse cx="8" cy="8" rx="3" ry="6.5"/><path d="M1.5 8h13M2.5 5h11M2.5 11h11"/></g></svg>
      </div>
    </div>
  </section>

</main>
</body>
</html>
```